Card Design for my dog training business Brightpaw Obedience

Need a business card design for my dog training business with my new logo. Want the card to come off professional yet fun. Want it to be very eye catchy as well. I normally have these at vet clinics, pet stores, and groomers. so need it to look better than my competitors.
Target Market(s)
dog owners
Industry/Entity Type
Dog Training
Contact Information for Business Card
needs logo, my name and info
Font styles to use
Serif
Colors
0255a3
ffffff
ec1f27
000000
333333
fbfbfb
Requirements
Must have
- Brightpaw Obedience
- Felix Orland
- 415 903 2276
- info@brightpawobedience.example
- www.brightpawobedience.example

```html
<!DOCTYPE html>
<html lang="en">
<head>
<meta charset="utf-8">
<title>Brightpaw Obedience — Business Card</title>
<link rel="stylesheet" href="https://fonts.googleapis.com/css2?family=Roboto:wght@400;500;700&family=Crimson+Text:ital@1&display=swap">
<style>
  :root {
    --page-bg: #e8e5e0;
    --card-white: #ffffff;
    --card-dark: #2a2828;
    --band-dark: #2b2929;
    --ink-light: #ffffff;
    --ink-dark: #1e1c1c;
    --shadow: rgba(0, 0, 0, 0.22);
  }
  * { box-sizing: border-box; margin: 0; padding: 0; }
  html, body {
    width: 1200px;
    height: 1040px;
    overflow: hidden;
    background: var(--page-bg);
  }
  .canvas {
    position: relative;
    width: 1200px;
    height: 1040px;
  }
  .card {
    position: absolute;
    left: 230px;
    width: 740px;
    height: 423px;
    box-shadow: 0 10px 28px var(--shadow);
    overflow: hidden;
  }
  .card--front { top: 70px; background: var(--card-white); }
  .card--back  { top: 547px; background: var(--card-dark); }

  /* front */
  .contact-band {
    position: absolute;
    top: 0;
    right: 80px;
    width: 390px;
    height: 250px;
    background: var(--band-dark);
    color: var(--ink-light);
    font-family: "Roboto", sans-serif;
    padding: 58px 0 0 40px;
  }
  .contact-band__name {
    font-weight: 700;
    font-size: 30px;
    letter-spacing: 0.2px;
    margin-bottom: 18px;
  }
  .contact-list { list-style: none; }
  .contact-list__item {
    display: flex;
    align-items: center;
    justify-content: space-between;
    width: 320px;
    font-size: 16px;
    font-weight: 400;
    line-height: 27px;
  }
  .contact-list__icon { width: 14px; height: 14px; flex: none; }

  .brand-mark {
    position: absolute;
    left: 70px;
    bottom: 70px;
    display: flex;
    align-items: center;
    gap: 12px;
    font-family: "Roboto", sans-serif;
    font-weight: 500;
    font-size: 26px;
    color: var(--ink-dark);
  }
  .brand-mark__square {
    width: 22px;
    height: 22px;
    background: var(--ink-dark);
  }

  /* back */
  .brand-mark--reverse {
    position: absolute;
    left: 0;
    right: 0;
    top: 160px;
    justify-content: center;
    color: var(--ink-light);
    font-size: 38px;
  }
  .brand-mark--reverse .brand-mark__square { background: var(--ink-light); width: 28px; height: 28px; }
  .tagline {
    position: absolute;
    left: 0;
    right: 0;
    bottom: 50px;
    text-align: center;
    font-family: "Crimson Text", serif;
    font-style: italic;
    font-size: 22px;
    color: var(--ink-light);
  }
</style>
</head>
<body>
<main class="canvas">
  <section class="card card--front" aria-label="Card front">
    <div class="contact-band">
      <h1 class="contact-band__name">Felix Orland</h1>
      <ul class="contact-list">
        <li class="contact-list__item">
          <span>415 903 2276</span>
          <svg class="contact-list__icon" viewBox="0 0 16 16" aria-hidden="true"><path d="M4 1.5 6.5 4 5 6c1 2 3 4 5 5l2-1.5 2.5 2.5-2 2.5C7 14 2 9 1.5 3.5Z" fill="#fff"/></svg>
        </li>
        <li class="contact-list__item">
          <span>info@brightpawobedience.example</span>
          <svg class="contact-list__icon" viewBox="0 0 16 16" aria-hidden="true"><rect x="1" y="3" width="14" height="10" fill="#fff"/><path d="M1.5 3.5 8 9l6.5-5.5" stroke="#2b2929" stroke-width="1.4" fill="none"/></svg>
        </li>
        <li class="contact-list__item">
          <span>www.brightpawobedience.example</span>
          <svg class="contact-list__icon" viewBox="0 0 16 16" aria-hidden="true"><circle cx="8" cy="8" r="7" fill="#fff"/><path d="M1 8h14M8 1c-3 3.5-3 10.5 0 14M8 1c3 3.5 3 10.5 0 14" stroke="#2b2929" stroke-width="1" fill="none"/></svg>
        </li>
      </ul>
    </div>
    <div class="brand-mark">
      <span class="brand-mark__square"></span>
      <span>Brightpaw Obedience</span>
    </div>
  </section>

  <section class="card card--back" aria-label="Card back">
    <div class="brand-mark brand-mark--reverse">
      <span class="brand-mark__square"></span>
      <span>Brightpaw Obedience</span>
    </div>
    <p class="tagline">“Patient training for happy dogs, one lesson at a time.”</p>
  </section>
</main>
</body>
</html>
```